Form With Marla - Health and Wellness Business Card and Logo

I need a business card design with a logo for my business you can check out at www.formwithmarla.net. I want something more original, simplistic, and memorable than the basic logo I have on my site currently. I am a health and wellness coach and I offer mindset coaching and nutrition plans. I like the colour teal and dark grey/black for my theme colours. I emphasize growth, longterm change, and the whole package of "healthy mind, healthy body, healthy life". I had played around the idea of intertwining 3 M's or incorporating growth (leaves etc.) into my design. I want my expertise and experience to show through. In one glance I want people to understand with confidence I can help them accomplish anything they set their minds to. I look forward to seeing what everyone comes up with!

Industry/Entity Type

Health And Wellness

Contact Information for Business Card

Form With Marla
Marla Prentiss
BSc, Health & Wellness Coach
"Manifest your best"
www.formwithmarla.net
formwithmarla@quillpost.net
472-618-9043

Colors
33b8a4
ffffff
333333
000000

Requirements
Must have
• A memorable and unique logo for my business!
Nice to have
• Could have the phrase "Are you unhappy with your body and state of health?" or "It takes the right skills to develop habits in order to create long term change. I can help you get there."

```html
<!DOCTYPE html>
<html lang="en">
<head>
<meta charset="utf-8">
<title>Form With Marla – Business Card</title>
<link href="https://fonts.googleapis.com/css2?family=Oswald:wght@500&family=Open+Sans:wght@300;400;600&display=swap" rel="stylesheet">
<style>
  :root {
    --backdrop: #1c1c1c;
    --card: #2a2a2a;
    --card-edge: #333333;
    --ink: #ffffff;
    --ink-soft: #d9d9d9;
    --teal: #1f8f8a;
    --rule: #8a8a8a;
    --mark: #bdbdbd;
  }
  * { margin: 0; padding: 0; box-sizing: border-box; }
  html, body {
    width: 1200px; height: 1000px; overflow: hidden;
    background: var(--backdrop);
  }
  .canvas {
    position: relative; width: 1200px; height: 1000px;
    display: flex; flex-direction: column; align-items: center; justify-content: center; gap: 40px;
  }
  .card {
    position: relative; width: 700px; height: 400px;
    background: var(--card);
    border: 1px solid var(--card-edge);
    box-shadow: 0 12px 30px rgba(0,0,0,0.5);
  }

  /* Back side: brand mark */
  .card-back { display: flex; flex-direction: column; align-items: center; justify-content: center; gap: 18px; }
  .brand-circle {
    width: 90px; height: 90px; border-radius: 50%;
    border: 2px solid var(--mark);
  }
  .brand-name {
    font-family: "Open Sans", sans-serif; font-weight: 400;
    font-size: 22px; letter-spacing: 3px; color: var(--mark);
  }

  /* Front side: contact details */
  .identity {
    position: absolute; right: 420px; top: 132px; text-align: right;
  }
  .person-name {
    font-family: "Oswald", sans-serif; font-weight: 500;
    font-size: 38px; line-height: 1.05; letter-spacing: 1px;
    color: var(--ink); text-transform: uppercase; white-space: nowrap;
  }
  .person-role {
    font-family: "Open Sans", sans-serif; font-weight: 600;
    font-size: 21px; color: var(--teal); letter-spacing: 1px;
  }
  .divider {
    position: absolute; left: 300px; top: 135px; width: 2px; height: 92px;
    background: var(--rule);
  }
  .contacts {
    position: absolute; left: 322px; top: 136px; list-style: none;
    font-family: "Open Sans", sans-serif; font-weight: 300;
    font-size: 19px; color: var(--ink-soft);
  }
  .contacts li { display: flex; align-items: center; gap: 14px; height: 31px; }
  .contacts svg { width: 16px; height: 16px; fill: var(--teal); flex: none; }
  .accent { color: var(--teal); }
  .address {
    position: absolute; left: 200px; top: 318px;
    display: flex; align-items: center; gap: 12px;
    font-family: "Open Sans", sans-serif; font-weight: 300;
    font-size: 19px; color: var(--ink-soft); letter-spacing: 0.5px;
  }
  .address svg { width: 16px; height: 20px; fill: var(--teal); }
</style>
</head>
<body>
<main class="canvas">

  <section class="card card-back" aria-label="Card back">
    <div class="brand-circle"></div>
    <p class="brand-name">Form With Marla</p>
  </section>

  <section class="card card-front" aria-label="Card front">
    <div class="identity">
      <h1 class="person-name">Marla Prentiss</h1>
      <p class="person-role">Director</p>
    </div>
    <div class="divider"></div>
    <ul class="contacts">
      <li>
        <svg viewBox="0 0 16 16" aria-hidden="true"><path d="M3.5 1.5l2.5 0 1.2 3.2-1.6 1.1c.8 1.7 2 2.9 3.6 3.6l1.1-1.6 3.2 1.2 0 2.5c0 .8-.7 1.5-1.5 1.5C6.8 13 3 9.2 2 3c0-.8.7-1.5 1.5-1.5z"/></svg>
        472-618-9043
      </li>
      <li>
        <svg viewBox="0 0 16 16" aria-hidden="true"><path d="M1 3h14v1.2L8 8.6 1 4.2z M1 5.6l7 4.4 7-4.4V13H1z"/></svg>
        formwithmarla@quillpost.net
      </li>
      <li>
        <svg viewBox="0 0 16 16" aria-hidden="true"><circle cx="8" cy="8" r="7"/><path d="M1 8h14M8 1c-3 3-3 11 0 14M8 1c3 3 3 11 0 14" stroke="#2a2a2a" stroke-width="1.1" fill="none"/></svg>
        <span>www.<span class="accent">formwithmarla</span>.net</span>
      </li>
    </ul>
    <p class="address">
      <svg viewBox="0 0 16 20" aria-hidden="true"><path d="M8 0C3.6 0 0 3.4 0 7.6 0 13 8 20 8 20s8-7 8-12.4C16 3.4 12.4 0 8 0zm0 10.5a3 3 0 110-6 3 3 0 010 6z"/></svg>
      18 Linden Row, Singapore, 5820
    </p>
  </section>

</main>
</body>
</html>
```